Letterhead Design for Law Firm

**Edit: I have added the photo of a bottom that I like.

------
We are looking for a re-design of our new letterhead. The letterhead is for a law firm and will be used for digital and traditionally printed correspondence.

Here are some suggestions:

- Please use colours are #8ec900 and simple black.
- Please do not use any type of "waves" at the bottom of the page. This is not in style at all.
- Please stay modern yet conservative.
- Please use font Segoe UI Light or similar if you can
- Avoid clipart or illustrations.
- Utilize ample white space in the layout so the design looks clean and information is easy to read at a glance. Don't overcrowd the letterhead.
- Make sure the letterhead design is consistent with our brand identity (see corvelith.ca)
-Please, no black headers or footers.

I am attaching my current letterhead and signature for your convenience.

Remember, the letterhead is an extension of our professional identity. We are a successful firm and trial lawyers who correspond with insurers, judges, lawyers, courts, clients, etc. Make it new, modern, attractive, yet powerful and conservative.

It needs to be easily printable. I would like the bleed removed in print so the black bar the bottom crosses the page (but the text is not near the edges)
Updates

Low design quality

Target Market(s)

Clients, Government Offices, Judiciary, Lawyers, Insurance Companies, Colleagues.

Industry/Entity Type

Law

Other font styles liked:
• Segoe UI LIght, Calibri Light,

Colors
00AB8E
00BBA5
67D7C9
C6EFE9
E9F9F6

Requirements
Must have
• Everything that is on the letterhead now.
Nice to have
• Cutting Edge design, yet conservative.
Should not have
• law firm cliche design, images,

```html
<!DOCTYPE html>
<html lang="en">
<head>
<meta charset="utf-8">
<title>Varenne Personal Injury Lawyers – Letterhead</title>
<link rel="stylesheet" href="https://fonts.googleapis.com/css2?family=Open+Sans:wght@300;400&display=swap">
<style>
  :root {
    --paper: #f6f4f4;
    --ink: #1a1a1a;
    --ink-soft: #2b2b2b;
    --accent: #8ec900;
    --signature-tone: #d9d6d6;
  }
  * { margin: 0; padding: 0; box-sizing: border-box; }
  html, body { width: 935px; height: 1200px; overflow: hidden; background: var(--paper); }
  body { font-family: "Open Sans", "Segoe UI", sans-serif; font-weight: 300; color: var(--ink); }
  .letterhead { position: relative; width: 935px; height: 1200px; }
  .abs { position: absolute; white-space: nowrap; }

  .brand { left: 42px; top: 52px; font-weight: 400; color: var(--ink); }
  .brand-name { font-size: 44px; line-height: 50px; }
  .brand-tagline { font-size: 14px; line-height: 18px; margin-top: 4px; }

  .office { left: 448px; top: 68px; font-size: 14px; line-height: 19px; font-style: normal; }
  .contacts { left: 676px; top: 49px; font-size: 14px; line-height: 19px; }
  .contacts li { list-style: none; display: flex; align-items: center; gap: 8px; }
  .contacts svg { width: 12px; height: 12px; fill: var(--accent); }

  .meta-left { left: 49px; top: 163px; font-size: 15px; font-weight: 400; }
  .meta-right { right: 88px; top: 165px; font-size: 15px; font-weight: 300; }

  .rule { position: absolute; left: 49px; width: 834px; }
  .rule-black { height: 2px; background: var(--ink); }
  .rule-green { height: 2px; background: var(--accent); }

  .text { font-size: 15px; line-height: 20.5px; }
  .delivery { left: 49px; top: 231px; }
  .date { right: 62px; top: 238px; }
  .addressee { left: 49px; top: 270px; }
  .attention { left: 49px; top: 396px; }
  .salutation { left: 49px; top: 423px; }
  .re-label { left: 49px; top: 461px; }
  .re-subject { left: 330px; top: 461px; }

  .body-copy { position: absolute; left: 55px; width: 820px; top: 569px; font-size: 13.3px; line-height: 20.5px; text-align: justify; color: var(--ink-soft); }
  .body-copy p + p { margin-top: 20px; }

  .closing { left: 55px; top: 893px; font-size: 14px; line-height: 18px; }
  .signature { left: 55px; top: 945px; width: 255px; height: 46px; background: var(--signature-tone); }
  .signer { left: 60px; top: 1012px; font-size: 14px; line-height: 17.5px; }

  .footer { position: absolute; left: 0; width: 935px; top: 1128px; text-align: center; font-size: 15px; line-height: 23px; }
  .footer strong { font-weight: 400; }
</style>
</head>
<body>
<main class="letterhead">
  <header>
    <div class="abs brand">
      <div class="brand-name">VARENNE</div>
      <div class="brand-tagline">PERSONAL INJURY LAWYERS</div>
    </div>
    <address class="abs office">48 Ashgrove Street E., Suite 910<br>Brantmoor, ON&nbsp; L9K 3T2</address>
    <ul class="abs contacts">
      <li><svg viewBox="0 0 16 16"><path d="M3 1l3 3-2 2c1 2 3 4 5 5l2-2 3 3-2 3C6 14 2 10 1 3z"/></svg>905-555-0142</li>
      <li><svg viewBox="0 0 16 16"><rect x="4" y="1" width="8" height="4"/><rect x="1" y="6" width="14" height="6"/><rect x="4" y="10" width="8" height="5"/></svg>905-555-0187</li>
      <li><svg viewBox="0 0 16 16"><path d="M1 3h14v10H1z"/><path d="M1 3l7 6 7-6" fill="none" stroke="#fff" stroke-width="1.2"/></svg>Email: nadia@corvelith.ca</li>
      <li><svg viewBox="0 0 16 16"><circle cx="8" cy="8" r="7"/></svg>www.CORVELITH.ca</li>
    </ul>
    <div class="abs meta-left">Without Prejudice</div>
    <div class="abs meta-right">File Clerk: Nadia Kostrova</div>
    <div class="rule rule-black" style="top:196px"></div>
    <div class="rule rule-green" style="top:200px"></div>
  </header>

  <section>
    <div class="abs text delivery">By Email</div>
    <div class="abs text date">March 13, 2024</div>
    <div class="abs text addressee">Northvale Insurance Company<br>Claims Litigation Department<br>240 Orchard Lane North<br>P.O. Box 4100<br>Elmridge, ON&nbsp;&nbsp; N3K 2P7</div>
    <div class="abs text attention">Attention:&nbsp; Mr. Delan Ward</div>
    <div class="abs text salutation">Mr. Ward:</div>
    <div class="abs text re-label">Re:</div>
    <div class="abs text re-subject">Harwick v. Benotti et al.<br>DOL:&nbsp; September 12, 2019<br>Pre-Mediation Settlement Proposal – March 13th, 2024</div>

    <div class="body-copy">
      <p>Lorem ipsum dolor sit amet, consectetur adipiscing elit. Donec orci purus, luctus vitae dignissim eu, iaculis sed purus. Vivamus faucibus, ipsum nec aliquet viverra, leo mauris condimentum ligula, sit amet sagittis enim ligula quis arcu. Nam egestas tortor ivisi porttitor mattis. In tortor ante, ultricies in suscipit a, tempus non massa. Vivamus et auctor mi. Fusce vel massa nulla. Phasellus nec eros mauris, et scelerisque orci.</p>
      <p>Donec malesuada orci vitae nulla accumsan porta a id massa. Quisque accumsan iaculis magna sit amet fringilla. Maecenas consequat, magna eget tincidunt semper, odio nibh rutrum mi, id feugiat ante nisi eu risus. Vestibulum nunc orci, rhoncus a placerat in, ultricies in mi. Cras mattis varius eros, vel fringilla nisi suscipit eget. Quisque scelerisque sagittis nulla at porttitor.</p>
      <p>Sed id augue vitae urna euismod commodo aliquet a quam. Pellentesque arcu velit, cursus et malesuada ut, consequat et diam. Nullam erat sem, rhoncus id ullamcorper vitae, rhoncus et arcu. In ultricies ultricies nulla, ut rutrum nisi iaculis at. Donec eu magna a metus ornare faucibus. Fusce aliquet faucibus ultricies. Morbi semper, est id tincidunt gravida, sem arcu adipiscing lacus, ac bibendum nulla leo eu purus. Quisque nec diam sed risus consectetur a ccumsan quis quis nibh. Vestibulum id purus lorem.</p>
    </div>

    <div class="abs closing">Yours very truly,<br>VARENNE PERSONAL INJURY LAWYERS</div>
    <div class="abs signature" role="img" aria-label="Handwritten signature of Paul D. Varenne"></div>
    <div class="abs signer">Paul D. Varenne<br>Varenne Law Professional Corporation<br>/nk<br>Encl.</div>
  </section>

  <footer>
    <div class="rule rule-black" style="top:1098px"></div>
    <div class="rule rule-green" style="top:1102px"></div>
    <div class="footer"><strong>Practice Restricted</strong>- Serious Personal Injury, Wrongful Death Litigation<br>Long-Term Disability Litigation, Wrongful Dismissal Litigation, Employee Terminations</div>
  </footer>
</main>
</body>
</html>
```